Card design for orthopaedic surgeons working as The Brightwater Joint Centre

Business cards, letterhead

Colors

Designer to choose colors to be used in the design.

Requirements
Must have
• Late addition.
• Cards letterhead must have logos of
• Crestmoor Lindell College of Surgeons
• Varenwood Bone Health Association
Nice to have
• Back of card to have space for appointment time to be added by hand and some blank space for writing incidental other notes.

```html
<!DOCTYPE html>
<html lang="en">
<head>
<meta charset="utf-8">
<title>The Brightwater Joint Centre – Stationery</title>
<link href="https://fonts.googleapis.com/css2?family=Roboto:wght@400;500&display=swap" rel="stylesheet">
<style>
:root{
  --stage:#999999;
  --paper:#ffffff;
  --brand-blue:#4aa3df;
  --brand-navy:#0a2d44;
  --ink:#1d2a36;
  --badge-tone:#e3ddd0;
  --rule:#4aa3df;
}
*{margin:0;padding:0;box-sizing:border-box}
html,body{width:1200px;height:763px;overflow:hidden;background:var(--stage);font-family:'Roboto',sans-serif;color:var(--ink)}
.canvas{position:relative;width:1200px;height:763px}
.business-card,.appointment-card,.letterhead{position:absolute;background:var(--paper);overflow:hidden}
.business-card,.appointment-card{left:91px;width:399px;height:234px;border-radius:12px;border:1px solid #cfcfcf}
.business-card{top:134px}
.appointment-card{top:390px}
.letterhead{left:523px;top:17px;width:571px;height:725px}
.wordmark{position:absolute;color:var(--brand-blue);font-weight:400;white-space:nowrap;letter-spacing:-0.2px}
.badge{position:absolute;background:var(--badge-tone);border-radius:6px}
.wave{position:absolute;left:0;top:0;width:100%;height:100%;pointer-events:none}
.abs{position:absolute;white-space:nowrap}
.divider{position:absolute;left:215px;top:61px;width:1px;height:112px;background:var(--rule)}
.person-name{left:229px;top:58px;font-size:13px;font-weight:500;color:var(--brand-blue)}
.person-title{left:229px;top:74px;font-size:9.6px;font-weight:500}
.contact{font-size:9.6px;line-height:12.6px}
.contact-line{display:flex;align-items:center;gap:3px;height:15px}
.contact-line svg{width:7px;height:7px;flex:none}
.heading{left:23px;top:38px;font-size:13px;font-weight:500;color:var(--brand-navy)}
.heading .accent{color:var(--brand-blue)}
.field{position:absolute;left:23px;right:21px;display:flex;align-items:flex-end;font-size:10.6px;gap:3px}
.fill{flex:1;border-bottom:1px dotted #444;height:1px;margin-bottom:2px}
.fill.fixed{flex:none}
.box{display:inline-block;width:7px;height:7px;border:1.2px solid var(--ink);margin-right:4px;vertical-align:-0.5px}
.days{position:absolute;left:23px;right:21px;top:138px;display:flex;justify-content:space-between;font-size:10px}
.reminder{left:23px;top:206px;font-size:10px}
</style>
</head>
<body>
<div class="canvas">

  <!-- Business card front -->
  <section class="business-card">
    <div class="wordmark" style="left:27px;top:65px;font-size:12px">The Brightwater Joint Centre</div>
    <div class="badge" role="img" aria-label="Crestmoor Lindell College of Surgeons crest" style="left:34px;top:97px;width:66px;height:80px"></div>
    <div class="badge" role="img" aria-label="Varenwood Bone Health Association badge" style="left:117px;top:100px;width:82px;height:76px"></div>
    <div class="divider"></div>
    <div class="abs person-name">Dana Whitcombe</div>
    <div class="abs person-title">President</div>
    <div class="abs contact" style="left:229px;top:97px">48 Harrowgate Ridge Road<br>Suite 310, Elmcrest, OR 97412</div>
    <div class="abs contact" style="left:229px;top:130px">
      <div class="contact-line"><svg viewBox="0 0 10 10"><path d="M2 1l2 2-1 1.2c.6 1.2 1.5 2.1 2.8 2.8L7 6l2 2-1.3 1.3C4.5 9 1 5.5.7 2.3z" fill="var(--brand-blue)"/></svg>555 210 4388</div>
      <div class="contact-line"><svg viewBox="0 0 10 10"><rect x="0.5" y="2" width="9" height="6" fill="var(--brand-blue)"/><path d="M0.5 2l4.5 3.5L9.5 2" stroke="#fff" fill="none" stroke-width="0.8"/></svg>hello@brightwaterjoint.com</div>
      <div class="contact-line"><svg viewBox="0 0 10 10"><circle cx="5" cy="5" r="4.2" fill="none" stroke="var(--brand-blue)"/><path d="M1 5h8M5 1c-2 2.5-2 5.5 0 8M5 1c2 2.5 2 5.5 0 8" fill="none" stroke="var(--brand-blue)" stroke-width="0.7"/></svg>www.brightwaterjoint.com</div>
    </div>
    <svg class="wave" viewBox="0 0 399 234" preserveAspectRatio="none" aria-hidden="true">
      <path d="M0,204 C100,186 200,214 300,221 C350,224 380,214 399,205 L399,234 L0,234Z" fill="var(--brand-blue)"/>
      <path d="M0,217 C90,198 200,220 300,226 C350,229 380,219 399,208 L399,234 L0,234Z" fill="var(--brand-navy)"/>
    </svg>
  </section>

  <!-- Business card back: appointment -->
  <section class="appointment-card">
    <div class="abs heading"><span class="accent">Next</span> Appointment</div>
    <div class="wordmark" style="right:22px;top:38px;font-size:12px">The Brightwater Joint Centre</div>
    <div class="field" style="top:92px"><span>Name:</span><span class="fill"></span></div>
    <div class="field" style="top:114px">
      <span>Date:</span><span class="fill fixed" style="width:118px"></span>
      <span>&nbsp;Time:</span><span class="fill"></span>
      <span>&nbsp;<span class="box"></span>AM</span><span>&nbsp;<span class="box"></span>PM</span>
    </div>
    <div class="days">
      <span><span class="box"></span>MON</span><span><span class="box"></span>TUES</span><span><span class="box"></span>WED</span>
      <span><span class="box"></span>THUR</span><span><span class="box"></span>FRI</span><span><span class="box"></span>SAT</span>
    </div>
    <div class="field" style="top:159px"><span>Note:</span><span class="fill"></span></div>
    <div class="field" style="top:180px"><span class="fill"></span></div>
    <div class="abs reminder">If you are unable to keep your appointment, please call us as soon as possible</div>
  </section>

  <!-- Letterhead -->
  <section class="letterhead">
    <div class="wordmark" style="left:37px;top:58px;font-size:15.6px">The Brightwater Joint Centre</div>
    <div class="badge" role="img" aria-label="Crestmoor Lindell College of Surgeons crest" style="left:370px;top:24px;width:61px;height:66px"></div>
    <div class="badge" role="img" aria-label="Varenwood Bone Health Association badge" style="left:452px;top:26px;width:70px;height:63px"></div>
    <div class="abs contact" style="left:35px;top:624px;font-size:10px;line-height:14.4px">48 Harrowgate Ridge Road<br>Suite 310, Elmcrest, OR 97412</div>
    <div class="abs contact" style="left:35px;top:659px;font-size:10px">
      <div class="contact-line" style="height:14px"><svg viewBox="0 0 10 10"><path d="M2 1l2 2-1 1.2c.6 1.2 1.5 2.1 2.8 2.8L7 6l2 2-1.3 1.3C4.5 9 1 5.5.7 2.3z" fill="var(--brand-blue)"/></svg>555 210 4388</div>
      <div class="contact-line" style="height:14px"><svg viewBox="0 0 10 10"><rect x="0.5" y="2" width="9" height="6" fill="var(--brand-blue)"/><path d="M0.5 2l4.5 3.5L9.5 2" stroke="#fff" fill="none" stroke-width="0.8"/></svg>hello@brightwaterjoint.com</div>
      <div class="contact-line" style="height:14px"><svg viewBox="0 0 10 10"><circle cx="5" cy="5" r="4.2" fill="none" stroke="var(--brand-blue)"/><path d="M1 5h8M5 1c-2 2.5-2 5.5 0 8M5 1c2 2.5 2 5.5 0 8" fill="none" stroke="var(--brand-blue)" stroke-width="0.7"/></svg>www.brightwaterjoint.com</div>
    </div>
    <svg class="wave" viewBox="0 0 571 725" preserveAspectRatio="none" aria-hidden="true">
      <path d="M0,725 L0,712 C150,712 350,678 470,680 C520,681 550,690 571,699 L571,725Z" fill="var(--brand-blue)"/>
      <path d="M0,691 C60,708 120,714 200,712 C320,708 420,689 480,691 C520,693 550,704 571,713 L571,725 L0,725Z" fill="var(--brand-navy)"/>
    </svg>
  </section>

</div>
</body>
</html>
```